2 sided postcard for New Internet Customers

We would like a design for a two sided postcard (with room for mailing label), dimensions 9 1/4 by 6 1/4 to be sent via US Mail.

The postcard needs to include our logo (attached) and the text
Fiber Optic Internet
555-318-2094
http://www.brightmesh.example
Speeds up to 1 Gig, with packages starting at $55

These will be sent to people who do not have our service.

Since this is going to be "junk mail" we probably only have 1 second or less to capture someone's attention to encourage them to read the entire postcard.

We are a "mom and pop" telecommunications company that provides internet, phone, and television services on the fiber optic network that we designed, built, and maintain.

We started as a dial up ISP in 1995, and have extraordinary technical support based in Freeport PA, our customers actually get the speeds they pay for, and our service is highly reliable.

We have a slogan (which you can choose to use or ignore) which is
"I Got Zoomed with Pellworth"

Existing customers can earn a $50 credit for every new customer they refer to us. Unlike most large cable and internet companies we have very happy customers... some who have stayed with us for decades.

I've attached our previous postcard, which I really dislike. It does have a blank spot for where the mailing label should go.

Target Market(s)

New Internet Customers in Western Pennsylvania

Industry/Entity Type

Internet

Font styles to use
Other font styles liked:
• Just match our logo.

Colors

Designer to choose colors to be used in the design.

Requirements
Must have
• The postcard needs to include our logo, and the text Fiber Optic Internet 555-318-2094 http://www.brightmesh.example Speeds up to 1 Gig, with packages starting at $55
Nice to have
• The colors and fonts should look good with our logo.
Should not have
• Should not have small print or lots of text. Both sides need to capture attention.

```html
<!DOCTYPE html>
<html lang="en">
<head>
<meta charset="utf-8">
<title>Pellworth Fiber Optic Internet Postcard</title>
<link rel="stylesheet" href="https://fonts.googleapis.com/css2?family=Montserrat:ital,wght@0,300;0,400;0,600;0,700;0,800;0,900;1,400;1,800;1,900&display=swap">
<style>
  :root {
    --bg: #d3d4d6;
    --blue: #1466c0;
    --blue-deep: #1b2a8f;
    --navy: #101a5c;
    --cyan: #1ea7ea;
    --red: #d9261c;
    --red-dark: #a8140d;
    --ink: #121212;
    --white: #ffffff;
    --stamp: #eceef1;
    --band: #0a0a0a;
  }
  * { margin: 0; padding: 0; box-sizing: border-box; }
  html, body { width: 1200px; height: 2812px; overflow: hidden; }
  body { background: var(--bg); font-family: "Montserrat", sans-serif; position: relative; }

  .card { position: absolute; left: 100px; width: 1000px; height: 666px; overflow: hidden; background: var(--white); }
  .card--front { top: 1048px; }
  .card--back { top: 1429px; }
  .card--front { top: 690px; }
  .card--back { top: 1426px; }
  .card svg.card-bg { position: absolute; inset: 0; }
  .abs { position: absolute; }

  /* front */
  .brand { left: 138px; top: 38px; display: flex; align-items: center; gap: 16px; color: var(--white); }
  .brand__dot { width: 80px; height: 80px; border-radius: 50%; background: var(--white); }
  .brand__name { font-size: 36px; font-weight: 300; line-height: 1; }
  .brand__site { font-size: 19px; font-weight: 400; margin-top: 6px; }
  .headline { left: 48px; top: 130px; color: var(--white); font-weight: 900; font-size: 70px; line-height: 1; letter-spacing: 1px; }
  .headline__box { display: inline-block; margin-top: 10px; padding: 2px 24px 4px; background: var(--cyan); border: 5px solid var(--navy); border-radius: 10px; color: var(--white); font-size: 76px; }
  .fiber-art { left: 525px; top: 0; width: 475px; height: 370px;
    background: radial-gradient(ellipse at 55% 45%, #6fb8ff 0%, #2a4fc4 35%, rgba(27,42,143,0) 70%); }
  .speeds { left: 690px; top: 365px; color: var(--white); font-style: italic; font-weight: 900; }
  .speeds__title { font-size: 56px; line-height: 1; }
  .speeds__row { display: flex; align-items: flex-start; gap: 10px; }
  .speeds__small { color: var(--cyan); font-size: 30px; font-weight: 800; margin-top: 6px; }
  .speeds__big { font-size: 110px; line-height: 0.9; font-style: normal; }
  .contact { left: 60px; color: var(--ink); display: flex; align-items: center; gap: 16px; }
  .contact--phone { top: 500px; font-size: 44px; font-weight: 700; }
  .contact--web { top: 566px; font-size: 30px; font-weight: 400; }
  .price { left: 530px; top: 452px; width: 160px; height: 160px; border-radius: 50%;
    background: radial-gradient(circle at 40% 35%, #f04a3c, var(--red) 55%, var(--red-dark));
    box-shadow: 0 4px 10px rgba(0,0,0,0.35); color: var(--white); text-align: center; font-style: italic; }
  .price__label { font-size: 20px; font-weight: 400; line-height: 1.1; margin-top: 26px; }
  .price__value { font-size: 58px; font-weight: 800; font-style: normal; line-height: 1.1; }

  /* back */
  .slogan { left: 36px; top: 28px; color: var(--white); font-size: 29px; font-weight: 800; text-transform: uppercase; }
  .about { left: 36px; top: 76px; width: 540px; color: var(--white); font-size: 13px; line-height: 1.3; }
  .about p + p { margin-top: 10px; }
  .photo { left: 250px; top: 160px; width: 300px; height: 416px; border-radius: 140px 140px 0 0;
    background: linear-gradient(180deg, #c9a07a 0%, #f2c318 45%, #f4cc20 70%, #2a2a2a 100%); }
  .credit { left: 98px; top: 160px; width: 230px; height: 230px; border-radius: 50%;
    background: radial-gradient(circle at 40% 35%, #f04a3c, var(--red) 55%, var(--red-dark));
    border: 4px solid var(--white); color: var(--white); text-align: center; font-weight: 800; }
  .credit__label { font-size: 18px; line-height: 1.05; margin-top: 26px; text-transform: uppercase; }
  .credit__value { font-size: 88px; line-height: 1; }
  .credit__unit { font-size: 20px; text-align: right; margin-right: 46px; }
  .refer { left: 28px; top: 362px; width: 164px; height: 164px; border-radius: 50%; background: var(--cyan);
    color: var(--ink); font-weight: 800; font-size: 19px; line-height: 1; padding: 38px 0 0 28px; text-transform: uppercase; }
  .stamp { left: 876px; top: 44px; width: 92px; height: 92px; background: var(--stamp); }
  .sign { left: 672px; top: 472px; display: flex; align-items: center; gap: 16px; color: var(--blue); font-size: 38px; font-weight: 700; }
  .sign__dot { width: 88px; height: 88px; border-radius: 50%; background: var(--blue); }
  .band { left: 0; top: 576px; width: 1000px; height: 90px; background: var(--band); display: flex; align-items: center; gap: 34px; padding-left: 60px; color: var(--white); font-size: 32px; white-space: nowrap; }
  .band__item { display: flex; align-items: center; gap: 12px; }
  .band__phone { font-weight: 700; }
  .icon { width: 30px; height: 30px; flex: none; }
</style>
</head>
<body>

<section class="card card--front" aria-label="Postcard front">
  <svg class="card-bg" width="1000" height="666" viewBox="0 0 1000 666">
    <defs>
      <linearGradient id="frontBlue" x1="0" y1="0" x2="1" y2="0.3">
        <stop offset="0" stop-color="#1572c8"/>
        <stop offset="0.55" stop-color="#1a5fc0"/>
        <stop offset="1" stop-color="#1b2a8f"/>
      </linearGradient>
    </defs>
    <rect width="1000" height="666" fill="url(#frontBlue)"/>
    <path d="M0,520 C140,390 340,340 540,380 C720,420 820,530 1000,580 L1000,666 L0,666 Z" fill="#1b2a8f"/>
    <path d="M0,550 C130,420 330,362 520,394 C700,426 820,550 1000,602 L1000,666 L0,666 Z" fill="#ffffff"/>
    <path d="M930,666 C960,550 990,450 1000,420 L1000,666 Z" fill="#ffffff"/>
  </svg>

  <div class="abs brand">
    <span class="brand__dot"></span>
    <div>
      <div class="brand__name">Pellworth, Inc.</div>
      <div class="brand__site">www.pellworth.example</div>
    </div>
  </div>

  <div class="abs fiber-art" role="img" aria-label="Glowing fiber optic cable with colourful strands"></div>

  <h1 class="abs headline">FIBER OPTIC<br><span class="headline__box">INTERNET</span></h1>

  <div class="abs speeds">
    <div class="speeds__title">SPEEDS</div>
    <div class="speeds__row">
      <span class="speeds__small">UP TO</span>
      <span class="speeds__big">1</span>
      <span class="speeds__small">GIG</span>
    </div>
  </div>

  <div class="abs contact contact--phone">
    <svg class="icon" viewBox="0 0 34 34"><circle cx="17" cy="17" r="17" fill="#1466c0"/><path d="M11 9c1 0 2 3 2 4s-2 1-1 3 3 4 5 5 2-1 3-1 4 1 4 2-2 3-4 3c-5 0-12-7-12-12 0-2 2-4 3-4z" fill="#fff"/></svg>
    <span>555-318-2094</span>
  </div>
  <div class="abs contact contact--web">
    <svg class="icon" viewBox="0 0 34 34"><circle cx="17" cy="17" r="17" fill="#1466c0"/><circle cx="17" cy="17" r="9" fill="none" stroke="#fff" stroke-width="2"/><path d="M8 17h18M17 8c-5 5-5 13 0 18M17 8c5 5 5 13 0 18" fill="none" stroke="#fff" stroke-width="2"/></svg>
    <span>www.brightmesh.example</span>
  </div>

  <div class="abs price">
    <div class="price__label">Packages<br>Starting at</div>
    <div class="price__value">$55</div>
  </div>
</section>

<section class="card card--back" aria-label="Postcard back">
  <svg class="card-bg" width="1000" height="666" viewBox="0 0 1000 666">
    <defs>
      <linearGradient id="backBlue" x1="0" y1="0" x2="1" y2="1">
        <stop offset="0" stop-color="#1466c0"/>
        <stop offset="1" stop-color="#1a58b8"/>
      </linearGradient>
    </defs>
    <rect width="1000" height="666" fill="#ffffff"/>
    <path d="M0,0 H600 C680,50 660,200 590,330 C530,440 500,540 500,576 H0 Z" fill="url(#backBlue)"/>
    <path d="M628,40 C690,110 660,230 600,340 C545,440 520,530 520,576" fill="none" stroke="#1466c0" stroke-width="5"/>
  </svg>

  <h2 class="abs slogan">I Got Zoomed with Pellworth</h2>
  <div class="abs about">
    <p>We are a family-run local company that provides internet, phone, and television on the fiber optic network we designed, built, and maintain.</p>
    <p>We began as a dial up provider in 1995, offer superb local support, deliver the speeds you pay for, and stay reliable.</p>
  </div>

  <div class="abs photo" role="img" aria-label="Surprised woman in a yellow shirt holding an open laptop"></div>

  <div class="abs refer">For<br>every new<br>customer<br>they refer<br>to us.</div>

  <div class="abs credit">
    <div class="credit__label">Existing<br>customers<br>can earn a</div>
    <div class="credit__value">$50</div>
    <div class="credit__unit">CREDIT</div>
  </div>

  <div class="abs stamp" aria-label="Postage area"></div>

  <div class="abs sign">
    <span>Pellworth</span>
    <span class="sign__dot"></span>
  </div>

  <div class="abs band">
    <div class="band__item band__phone">
      <svg class="icon" viewBox="0 0 34 34"><circle cx="17" cy="17" r="17" fill="#1466c0"/><path d="M11 9c1 0 2 3 2 4s-2 1-1 3 3 4 5 5 2-1 3-1 4 1 4 2-2 3-4 3c-5 0-12-7-12-12 0-2 2-4 3-4z" fill="#fff"/></svg>
      <span>555-318-2094</span>
    </div>
    <div class="band__item">
      <svg class="icon" viewBox="0 0 34 34"><circle cx="17" cy="17" r="17" fill="#1466c0"/><circle cx="17" cy="17" r="9" fill="none" stroke="#fff" stroke-width="2"/><path d="M8 17h18M17 8c-5 5-5 13 0 18M17 8c5 5 5 13 0 18" fill="none" stroke="#fff" stroke-width="2"/></svg>
      <span>www.brightmesh.example</span>
    </div>
  </div>
</section>

</body>
</html>
```